Business card design for a dynamic IT consulting company

We need a business card design for a young firm, specialized in the Telecommunications/Consulting industry. The name of the company is Quindor and Partners Business Consulting Ltd. (Short name: Quindor and Partnes)
Quindor = solve read reverse, so we aim to be uncomplicated and solution-oriented. The small pipe in our logo is also related to the word solve. So we need a new business card design, which is simple, eye catching and something non traditional (I would probably prefer a square shaped design rather than a rectangle, but open for suggestions). Attached our logo.

Target Market(s)

Usually our customers are Tier1 Telecoms providers (Q-Netra, Palorix, etc) and their executives.

Industry/Entity Type

Business

Contact Information for Business Card

Name: Bence Tolnavari
Email: b.tolnavari@quindor.hu
Web: www.quindor.hu
Mobile: +36 30 518 2769
Title: Managing Director

Optional:
Company name: Quindor and Partners Ltd.
Address: 1087 Budapest, Tolvenka str. 28/C, Hungary

Font styles to use
Other font styles liked:
• helveticaneue_medium, Prime Regular are used now.

Colors

Designer to choose colors to be used in the design.

Requirements
Must have
• I would like to have a 2 sided design.
Nice to have
• I thought if we make the logo a bit bigger (without the company name), that could go to the back with the company name below. I though, if the pipe in the logo is somehow touchable on the business card, would be nice and unique.

```html
<!DOCTYPE html>
<html lang="en">
<head>
<meta charset="utf-8">
<title>Quindor and Partners – Business Card</title>
<link rel="stylesheet" href="https://fonts.googleapis.com/css2?family=Exo+2:wght@500&family=Roboto:wght@300;400&display=swap">
<style>
  :root {
    --bg: #ece9e6;
    --card: #ffffff;
    --ink: #2b2b2b;
    --grey: #6d6e71;
    --grey-soft: #9a9b9e;
    --blue: #1ca1dc;
    --magenta: #c3379b;
    --shadow: 0 18px 40px rgba(0,0,0,.18);
  }
  * { box-sizing: border-box; margin: 0; padding: 0; }
  html, body { width: 1200px; height: 900px; overflow: hidden; }
  body {
    background: var(--bg);
    font-family: "Roboto", Arial, sans-serif;
    color: var(--ink);
    position: relative;
  }
  .card {
    position: absolute;
    top: 200px;
    width: 500px;
    height: 500px;
    background: var(--card);
    border-radius: 30px;
    box-shadow: var(--shadow);
    overflow: hidden;
  }
  .card--back { left: 70px; }
  .card--front { left: 630px; }

  /* Company name */
  .company-name {
    position: absolute;
    font-family: "Roboto", Arial, sans-serif;
    font-weight: 300;
    color: var(--grey);
    line-height: 1;
    white-space: nowrap;
  }

  /* Back */
  .back__mark-area {
    position: absolute;
    left: 150px;
    top: 70px;
    width: 300px;
    height: 225px;
    border-radius: 6px;
    background: linear-gradient(135deg, #c3379b 0%, #1ca1dc 55%, #6d6e71 100%);
    opacity: .85;
  }
  .card--back .company-name { right: 50px; top: 338px; font-size: 40px; }
  .back__web {
    position: absolute;
    right: 50px;
    top: 400px;
    font-size: 15px;
    letter-spacing: 5px;
    color: var(--grey-soft);
  }

  /* Front */
  .card--front .company-name { left: 40px; top: 55px; font-size: 34px; }

  .person { position: absolute; left: 40px; top: 155px; }
  .person__name {
    font-family: "Exo 2", "Roboto", sans-serif;
    font-weight: 500;
    font-size: 28px;
    line-height: 1.1;
  }
  .person__first { color: var(--blue); }
  .person__last { color: var(--magenta); }
  .person__title { font-size: 19px; color: var(--grey); margin-top: 4px; font-weight: 300; }

  .contact { position: absolute; left: 40px; top: 240px; list-style: none; font-size: 17px; color: var(--ink); }
  .contact__item { display: flex; align-items: flex-start; height: 26.5px; }
  .contact__item--gap { margin-top: 14px; }
  .contact__icon { width: 14px; height: 16px; margin: 4px 11px 0 0; flex: none; }
  .contact__icon--none { visibility: hidden; }

  .front__mark-corner {
    position: absolute;
    right: 18px;
    bottom: 18px;
    width: 100px;
    height: 96px;
    border-radius: 4px;
    background: linear-gradient(135deg, #c3379b 0%, #1ca1dc 55%, #6d6e71 100%);
    opacity: .85;
  }
</style>
</head>
<body>

<section class="card card--back" aria-label="Card back">
  <div class="back__mark-area" role="img" aria-label="Large company symbol in magenta, blue and grey"></div>
  <div class="company-name">Quindor and Partners</div>
  <div class="back__web">www.quindor.hu</div>
</section>

<section class="card card--front" aria-label="Card front">
  <div class="company-name">Quindor and Partners</div>

  <div class="person">
    <div class="person__name"><span class="person__first">Bence</span> <span class="person__last">Tolnavari</span></div>
    <div class="person__title">Managing Director</div>
  </div>

  <ul class="contact">
    <li class="contact__item">
      <svg class="contact__icon" viewBox="0 0 14 16" aria-hidden="true"><path fill="#1ca1dc" d="M7 0a5.5 5.5 0 0 0-5.5 5.5C1.5 9.5 7 16 7 16s5.5-6.5 5.5-10.5A5.5 5.5 0 0 0 7 0zm0 7.6a2.1 2.1 0 1 1 0-4.2 2.1 2.1 0 0 1 0 4.2z"/></svg>
      <span>1087 Budapest</span>
    </li>
    <li class="contact__item">
      <svg class="contact__icon contact__icon--none" viewBox="0 0 14 16" aria-hidden="true"></svg>
      <span>Tolvenka út 28/C, Hungary</span>
    </li>
    <li class="contact__item contact__item--gap">
      <svg class="contact__icon" viewBox="0 0 14 16" aria-hidden="true"><path fill="#1ca1dc" d="M3 2.5 5 2l1.4 3-1.3 1.1a7 7 0 0 0 3.3 3.4L9.6 8.2l3 1.4-.5 2.1c-.2.6-.8 1-1.4.9C5.9 12 2.2 8.3 2.1 3.9c0-.7.3-1.2.9-1.4z"/></svg>
      <span>+ 36 30 742 1586</span>
    </li>
    <li class="contact__item">
      <svg class="contact__icon" viewBox="0 0 14 16" aria-hidden="true"><rect x="3" y="0.8" width="8" height="14.4" rx="1.5" fill="none" stroke="#1ca1dc" stroke-width="1.4"/><circle cx="7" cy="12.6" r="0.9" fill="#1ca1dc"/></svg>
      <span>+ 36 30 518 2769</span>
    </li>
    <li class="contact__item">
      <svg class="contact__icon" viewBox="0 0 14 16" aria-hidden="true"><rect x="0.5" y="4" width="13" height="9" fill="#1ca1dc"/><path d="M0.5 4 7 9l6.5-5" fill="none" stroke="#fff" stroke-width="1"/></svg>
      <span>b.tolnavari@quindor.hu</span>
    </li>
    <li class="contact__item">
      <svg class="contact__icon" viewBox="0 0 14 16" aria-hidden="true"><g fill="none" stroke="#1ca1dc" stroke-width="1"><circle cx="7" cy="8.5" r="6"/><ellipse cx="7" cy="8.5" rx="2.6" ry="6"/><path d="M1 8.5h12M2 5.5h10M2 11.5h10"/></g></svg>
      <span>www.quindor.hu</span>
    </li>
  </ul>

  <div class="front__mark-corner" role="img" aria-label="Small company symbol in magenta, blue and grey"></div>
</section>

</body>
</html>
```